Business Card: RW Office Partners - Your organised problem solver

Business Name: RW Office Partners
Website: www.rwofficepartners.com.au
Email: marisol@rwofficepartners.com.au
Mobile: 61 482 907 236
Facebook: @rwofficepartners
Instrgram: @rwofficepartners

Brading Colours:
HEX
#986474
#ddccd3
#7a8498
#c9d8e4
#000000
#ffffff

Tag Line: Your dependable desk partner

Link to DRAFT website:
https://deskhelpcollective.wixsite.com/rw-office-partners

About Page from the website:
My name is Marisol Wrenfield, and I would love to assist you to become more productive in your day to day and achieve your business and personal goals.
My mission is to give you time, time to work on the important tasks of your business or to be able to spend more time with your family. I will take on the tasks you don’t have time for, don’t know well or simply don’t like to do.
I have an extensive background in Administration, Tender Coordination, Document Control, WHS and Quality Management working primarily in the Construction, Mining and Corporate World.
I am passionate about being organised, having order and making things in your life (and mine) easier! I love to watch something unfold and grow into something amazing! I am known for being the go-to problem solver, the organiser of all things, producing high standards of work even under pressure. I’m also a confident communicator, and I understand that you’re busy running your business.

Target Market(s)

Small to Medium Business who require assistance in their business by a virtual assistant.

Industry/Entity Type

Virtual Assistant

Contact Information for Business Card

Mobile: 61 482 907 236

Font styles to use
Sans Serif

Colors
ffffff

Requirements
Must have
• Branding Colours as outlined.
Contact Details as outlined.
Logo as provided.
Proper contact details - mobile, facebook, instragm, website.
Simple, Elegant, very clean looking.
Should not have
• Note cute with pictures.
Not too girly as still want to market to construction companies.

```html
<!DOCTYPE html>
<html lang="en">
<head>
<meta charset="utf-8">
<title>RW Office Partners – Business Card</title>
<link rel="stylesheet" href="https://fonts.googleapis.com/css2?family=Montserrat:wght@600;700&family=Arimo:wght@400&display=swap">
<style>
  :root {
    --backdrop: #8a5634;
    --kraft-light: #d4b08a;
    --kraft-mid: #c49c72;
    --kraft-dark: #b48a60;
    --ink: #111111;
  }
  html, body {
    margin: 0;
    padding: 0;
    width: 1200px;
    height: 900px;
    overflow: hidden;
    background: var(--backdrop);
  }
  .canvas {
    position: relative;
    width: 1200px;
    height: 900px;
  }
  .card {
    position: absolute;
    width: 556px;
    height: 343px;
    background: radial-gradient(ellipse at 50% 20%, var(--kraft-light), var(--kraft-mid) 60%, var(--kraft-dark));
    box-shadow: 2px 3px 6px rgba(0,0,0,0.45);
    color: var(--ink);
  }
  .card--front { left: 330px; top: 90px; }
  .card--back  { left: 330px; top: 470px; }

  .brand-name {
    position: absolute;
    font-family: "Montserrat", sans-serif;
    font-weight: 700;
    letter-spacing: 0.5px;
    text-transform: uppercase;
    color: var(--ink);
    white-space: nowrap;
    line-height: 1;
    margin: 0;
  }
  .card--front .brand-name { left: 45px; top: 62px; font-size: 25px; }
  .card--back .brand-name { left: 0; right: 0; top: 157px; font-size: 27px; text-align: center; }

  .contact-list {
    position: absolute;
    left: 162px;
    top: 167px;
    margin: 0;
    padding: 0;
    list-style: none;
    font-family: "Arimo", sans-serif;
    font-size: 16px;
  }
  .contact-item {
    display: flex;
    align-items: center;
    gap: 6px;
    height: 25.5px;
  }
  .contact-item--social-first { margin-top: 10px; }
  .contact-item--social { height: 30px; }
  .contact-icon { width: 18px; height: 18px; flex: none; }
  .social-dot {
    width: 18px; height: 18px; flex: none;
    border: 1.5px solid var(--ink);
    border-radius: 50%;
    box-sizing: border-box;
    margin-left: -2px;
    margin-right: 4px;
  }
  .tagline {
    position: absolute;
    left: 0; right: 0;
    top: 283px;
    margin: 0;
    text-align: center;
    font-family: "Montserrat", sans-serif;
    font-weight: 700;
    font-size: 15.5px;
    line-height: 1;
    text-transform: uppercase;
  }
</style>
</head>
<body>
<main class="canvas">
  <section class="card card--front" aria-label="Business card front">
    <p class="brand-name">RW Office Partners</p>
    <ul class="contact-list">
      <li class="contact-item">
        <svg class="contact-icon" viewBox="0 0 18 18" aria-hidden="true"><rect x="1.5" y="1.5" width="15" height="15" rx="2" fill="none" stroke="#111" stroke-width="1.5"/><path d="M6 4.5c-1 .6-1.4 1.6-.9 3 .8 2.2 2.6 4.2 4.8 5.2 1.2.5 2.3.2 3-.8l-1.8-1.6-1.1.8c-1-.5-2.1-1.7-2.5-2.7l.8-1.1z" fill="#111"/></svg>
        <span>61 482 907 236</span>
      </li>
      <li class="contact-item">
        <svg class="contact-icon" viewBox="0 0 18 18" aria-hidden="true"><rect x="1" y="4" width="16" height="11" fill="#111"/><path d="M1 4l8 6 8-6" fill="none" stroke="#c9a27a" stroke-width="1.3"/></svg>
        <span>marisol@rwofficepartners.com.au</span>
      </li>
      <li class="contact-item">
        <svg class="contact-icon" viewBox="0 0 18 18" aria-hidden="true"><g fill="none" stroke="#111" stroke-width="1.4"><circle cx="9" cy="9" r="7.3"/><ellipse cx="9" cy="9" rx="3.2" ry="7.3"/><path d="M1.7 9h14.6M3 5h12M3 13h12"/></g></svg>
        <span>www.rwofficepartners.com.au</span>
      </li>
      <li class="contact-item contact-item--social contact-item--social-first">
        <span class="social-dot" aria-hidden="true"></span>
        <span>@rwofficepartners</span>
      </li>
      <li class="contact-item contact-item--social">
        <span class="social-dot" aria-hidden="true"></span>
        <span>@rwofficepartners</span>
      </li>
    </ul>
  </section>

  <section class="card card--back" aria-label="Business card back">
    <p class="brand-name">RW Office Partners</p>
    <p class="tagline">Your dependable desk partner</p>
  </section>
</main>
</body>
</html>
```